GlassHaven Artbook for Okanagan Region, British Columbia

Creating an art book: GlassHaven, for the Okanagan Wine Region in British Columbia, Canada. Would like smart, modern, clean and linear...cool, sexy urban, not ugly boring suburban... I need a cover that appeals to the wino in all of us! Title: GlassHaven -Marla Dovicki
Updates
Thank you all kindly for your efforts. I have added some files so that you can get a sense of my aesthetic...it's never easy trying to figure it out, is it? I will hopefully have dimensions of book soon...cheers, Marla
would anyone please design a giant wine bottle with the wine label that looks like a label but says glasshaven...just curious to see if it works as a design or not...thank you.
Target Market(s)
Designing this wine art book of quotes to wineries in Okanagan BC. Buyer is wine lover and tourist ready to spend his vacation bucks on this wonderful book!
Look and feel

```html
<!DOCTYPE html>
<html lang="en">
<head>
<meta charset="utf-8">
<title>GlassHaven — Cover</title>
<link href="https://fonts.googleapis.com/css2?family=Open+Sans:wght@700&family=Lato:wght@300&display=swap" rel="stylesheet">
<style>
  :root {
    --page: #ffffff;
    --cover: #e4e4e2;
    --title: #ffffff;
    --wine-red: #ed1c24;
    --author: #3a3a3a;
  }
  html, body {
    margin: 0;
    padding: 0;
    overflow: hidden;
    background: var(--page);
  }
  .canvas {
    position: relative;
    width: 1200px;
    height: 1000px;
    background: var(--page);
    overflow: hidden;
  }
  .book-cover {
    position: absolute;
    left: 363px;
    top: 157px;
    width: 470px;
    height: 651px;
    background: var(--cover);
  }
  .book-title {
    position: absolute;
    left: 0;
    right: 0;
    top: 193px;
    margin: 0;
    text-align: center;
    font-family: "Open Sans", sans-serif;
    font-weight: 700;
    font-size: 38px;
    letter-spacing: 0.07em;
    line-height: 1;
    color: var(--title);
    text-transform: uppercase;
    padding-left: 0.07em;
  }
  .cover-artwork {
    position: absolute;
    left: 164px;
    top: 309px;
    width: 146px;
    height: 97px;
    background: var(--wine-red);
  }
  .book-author {
    position: absolute;
    left: 0;
    right: 0;
    top: 562px;
    margin: 0;
    text-align: center;
    font-family: "Lato", sans-serif;
    font-weight: 300;
    font-size: 16px;
    letter-spacing: 0.2em;
    line-height: 1;
    color: var(--author);
    text-transform: uppercase;
    padding-left: 0.2em;
  }
</style>
</head>
<body>
<div class="canvas">
  <section class="book-cover">
    <h1 class="book-title">GlassHaven</h1>
    <div class="cover-artwork" role="img" aria-label="Illustration of three red wine bottles standing in a row"></div>
    <p class="book-author">Marla Dovicki</p>
  </section>
</div>
</body>
</html>
```